Web Developer Needs a Business Card Design

I need a personal business card design that represents me as a web developer for potential employers. I would like the background to be a dark color on the front for contrast with my logo and name. The back will have all my information along with a smaller version of the logo. I want something with a modern look and feel, not too conservative. This will be used for potential employers and freelance work.

Industry/Entity Type

Business

Contact Information for Business Card

Front should have my logo and name. The back should have all my personal information which would include: name: Tom Varulek, phone: 570-614-3098, email: tomvarulek@quillbox.net, website url: www.tomvarulek.net, logo, web developer.

Font styles to use
Sans Serif

Requirements
Must have
• Must include my logo. The color palette base color will be the logo color.

```html
<!DOCTYPE html>
<html lang="en">
<head>
<meta charset="utf-8">
<title>Tom Varulek – Business Card</title>
<link rel="stylesheet" href="https://fonts.googleapis.com/css2?family=Open+Sans:wght@400;600&display=swap">
<style>
  :root {
    --backdrop: #2a2a2a;
    --card-face: #e6e6e6;
    --card-face-light: #f1f1f1;
    --teal: #7fd3c2;
    --card-edge: #111111;
    --ink: #1c1c1c;
  }
  * { box-sizing: border-box; margin: 0; padding: 0; }
  html, body {
    width: 1200px; height: 903px; overflow: hidden;
    background: var(--backdrop);
    font-family: "Open Sans", sans-serif;
    color: var(--ink);
  }
  .stage {
    position: relative; width: 1200px; height: 903px;
  }
  .card {
    position: absolute;
    width: 520px; height: 298px;
    background: var(--card-edge);
    padding: 3px;
  }
  .card-inner {
    position: relative; width: 100%; height: 100%;
    border: 7px solid var(--teal);
    background: linear-gradient(160deg, var(--card-face-light), var(--card-face));
    overflow: hidden;
  }
  .card--info { left: 50px; top: 180px; }
  .card--front { left: 630px; top: 425px; }

  .logo-mark {
    position: absolute;
    display: flex; align-items: center; justify-content: center;
    border: 6px solid var(--teal); border-radius: 50%;
    color: var(--teal); font-weight: 600; line-height: 1;
  }
  .card--info .logo-mark {
    width: 86px; height: 86px; left: 210px; top: 22px; font-size: 34px;
  }
  .card--front .logo-mark {
    width: 118px; height: 118px; left: 194px; top: 42px; font-size: 46px;
  }

  .rule { position: absolute; background: var(--ink); }
  .rule--top { left: 300px; top: 92px; width: 190px; height: 2px; }
  .rule--bottom { left: 20px; top: 196px; width: 262px; height: 2px; }
  .rule--divider { left: 282px; top: 118px; width: 2px; height: 80px; }

  .identity {
    position: absolute; right: 234px; top: 138px;
    text-align: right;
  }
  .identity-name { font-size: 24px; line-height: 1.1; }
  .identity-role { font-size: 17px; line-height: 1.1; }

  .contact-list {
    position: absolute; left: 294px; top: 104px;
    list-style: none; font-size: 14.5px; line-height: 1.5;
  }
  .contact-list li { display: flex; align-items: center; gap: 5px; white-space: nowrap; }
  .contact-icon { width: 12px; height: 12px; flex: none; }

  .front-name {
    position: absolute; left: 0; right: 0; top: 196px;
    text-align: center; font-size: 38px;
  }
</style>
</head>
<body>
<main class="stage">

  <section class="card card--info" aria-label="Card back with contact details">
    <div class="card-inner">
      <div class="logo-mark">tv</div>
      <div class="rule rule--top"></div>
      <div class="rule rule--divider"></div>
      <div class="rule rule--bottom"></div>
      <div class="identity">
        <p class="identity-name">Tom Varulek</p>
        <p class="identity-role">web developer</p>
      </div>
      <ul class="contact-list">
        <li>
          <svg class="contact-icon" viewBox="0 0 12 12" aria-hidden="true"><rect width="12" height="12" rx="1.5" fill="#1c1c1c"/><path d="M3.4 2.6l1.4 1.6-.7.9c.5 1 1.3 1.8 2.3 2.3l.9-.7 1.6 1.4-.8 1.1C5.6 9 3 6.4 2.3 3.4z" fill="#fff"/></svg>
          570-614-3098
        </li>
        <li>
          <svg class="contact-icon" viewBox="0 0 12 12" aria-hidden="true"><rect width="12" height="12" rx="1.5" fill="#1c1c1c"/><rect x="2.2" y="3.4" width="7.6" height="5.2" fill="#fff"/><path d="M2.2 3.4L6 6.4l3.8-3" fill="none" stroke="#1c1c1c" stroke-width=".8"/></svg>
          tomvarulek@quillbox.net
        </li>
        <li>
          <svg class="contact-icon" viewBox="0 0 12 12" aria-hidden="true"><rect width="12" height="12" rx="1.5" fill="#1c1c1c"/><circle cx="6" cy="6" r="3.6" fill="none" stroke="#fff" stroke-width=".9"/><path d="M2.4 6h7.2M6 2.4c-1.6 2-1.6 5.2 0 7.2M6 2.4c1.6 2 1.6 5.2 0 7.2" fill="none" stroke="#fff" stroke-width=".7"/></svg>
          www.tomvarulek.net
        </li>
      </ul>
    </div>
  </section>

  <section class="card card--front" aria-label="Card front with logo and name">
    <div class="card-inner">
      <div class="logo-mark">tv</div>
      <p class="front-name">Tom Varulek</p>
    </div>
  </section>

</main>
</body>
</html>
```